web page template design

We'd like to see a few designs based on the selected logo. See attached color logo.

We'll need a homepage design which will display the competition announcement and limited details about it. There will be links (or tabs) to the follow on pages which will contain all of the legal details, sign-up and design submission page, finalist selection page, winner announcement page, jury (judges) background page, company sponsor (Velmar) details, press release page and a blog page. These are just guidelines for the number of subpage links.

So we'd like a primary page and a follow-on page which is a little more plain.

Here is the competition briefer below:

In January 2014, Velmar Tile Inc. will launch its 1st Annual Velmar Tile Floor Design Competition. This design competition will be open to Design and Architecture students of the NYC area. Students and student groups can submit cork flooring design concepts online to a judging committee of prominent designers and architects who will select design finalists and a winner. The winning design will highlight the unique creative possibilities of sustainable cork tiles. The winner will receive a cash prize and publication of their winning design through press releases and various media outlets as well as on the TileBrandt.com website. The winning floor will be created and photographed by Velmar Tile and will be donated to a deserving non-profit community center in NYC. The donated cork floor will be installed at no cost to the non-profit community center.

Target Market(s)

designers and architects.

Industry/Entity Type

Non-Profit

Requirements
Must have
• tabs or link system

```html
<!DOCTYPE html>
<html lang="en">
<head>
<meta charset="utf-8">
<title>Velmar Tile Floor Design Competition 2014</title>
<link href="https://fonts.googleapis.com/css2?family=Open+Sans:wght@300;400;600;700&display=swap" rel="stylesheet">
<style>
:root{
  --red:#c0393b;--orange:#d08e1c;--yellow:#f2c84b;--khaki:#d7d27f;--teal:#5aabb0;
  --ink:#333;--muted:#999;--nav:#555;--paper:#fff;--backdrop:#ececec;
  --footer:#111;--footer-bottom:#1c1c1c;--footer-text:#bbb;--band:#d6d6d6;--logo-gray:#8a8a8a;
}
*{margin:0;padding:0;box-sizing:border-box}
html,body{width:1108px;height:1200px;overflow:hidden}
body{background:var(--backdrop);font-family:"Open Sans",Arial,sans-serif;color:var(--ink)}
.stage{position:absolute;left:0;top:0;width:1200px;height:1300px;transform:scale(0.9233);transform-origin:0 0}
.page{position:absolute;left:105px;top:0;width:989px;height:1300px;background:var(--paper);box-shadow:0 0 18px rgba(0,0,0,.25)}
.abs{position:absolute}
.stripe{position:absolute;left:0;width:989px;display:flex}
.stripe span{display:block;height:100%}
.s1{background:var(--red);width:173px}.s2{background:var(--orange);width:209px}.s3{background:var(--yellow);width:208px}.s4{background:var(--khaki);width:208px}.s5{background:var(--teal);width:191px}
.brand{left:422px;top:25px;width:145px;height:96px;background:#f7f7f5;text-align:center}
.brand-dot{width:42px;height:42px;border-radius:50%;background:var(--orange);margin:4px auto 5px}
.brand-text{font-weight:700;color:#6b2a1c;line-height:1.05}
.brand-text .l1{font-size:11px}.brand-text .l2{font-size:7px;letter-spacing:2.6px}.brand-text .l3{font-size:8px}
.nav{top:128px;left:195px;display:flex;gap:0;font-size:8px;font-weight:600;text-transform:uppercase;color:var(--nav)}
.nav a{color:inherit;text-decoration:none;margin-right:14.5px}
.account{top:128px;left:693px;font-size:8px;font-weight:700;color:var(--red);text-transform:uppercase}
.account span{margin:0 12px}
.hero{left:0;top:150px;width:989px;height:334px;background:linear-gradient(100deg,#7d6a58 0%,#a48e78 25%,#8a735d 50%,#6e5a48 75%,#4c3d31 100%)}
.badge{left:203px;top:59px;width:101px;height:18px;background:var(--teal);color:#fff;font-size:7.5px;font-weight:700;line-height:18px;padding-left:8px}
.badge svg{vertical-align:-2px;margin-right:5px}
.hero h1{left:197px;top:86px;width:520px;font-size:38px;font-weight:300;line-height:45px;color:var(--yellow)}
.hero p{left:201px;top:190px;width:480px;font-size:11.3px;line-height:15.6px;color:#fff}
.btn{left:202px;top:259px;width:88px;height:35px;border:1px solid #fff;color:#fff;font-size:8px;font-weight:700;text-align:center;line-height:33px}
.sec-head{font-size:14.5px;color:var(--ink);display:flex;align-items:center;gap:6px}
.rule{height:1px;background:#cfcfcf}
.ann-title{left:204px;top:557px;width:140px;font-size:14.5px;line-height:19px}
.meta{font-size:8.5px;color:#aaa;font-weight:300}
.excerpt{left:204px;top:648px;width:145px;font-size:8.8px;line-height:15px;font-weight:300}
.excerpt a{color:var(--red);text-decoration:none}
.press{left:590px;top:504px;width:185px;height:254px;background:#fbfbfb}
.press-item{position:absolute;left:10px;width:170px}
.thumb{position:absolute;left:0;top:0;width:44px;height:44px}
.press-item .txt{position:absolute;left:54px;top:0;width:115px;font-size:8.8px;line-height:12.5px}
.press-item .meta{position:absolute;left:54px;top:33px}
.finalist{position:absolute;top:757px;width:133px}
.finalist .photo{width:133px;height:134px}
.finalist .name{margin-top:12px;text-align:center;font-size:9.5px;letter-spacing:.6px;text-transform:uppercase;color:#444}
.band{left:0;top:963px;width:989px;height:64px;background:var(--band)}
.partner{position:absolute;top:22px;font-size:15px;font-weight:600;color:var(--logo-gray)}
.footer{left:0;top:1037px;width:989px;height:208px;background:var(--footer)}
.foot-brand{left:163px;top:46px;width:135px;text-align:center;color:#fff}
.foot-brand .dot{width:38px;height:38px;border-radius:50%;background:#fff;margin:0 auto 8px}
.foot-brand .l1{font-size:10.5px;font-weight:700}.foot-brand .l2{font-size:6.5px;font-weight:700;letter-spacing:2.5px}.foot-brand .l3{font-size:7.5px;font-weight:700}
.col h3{font-size:11.5px;font-weight:400;color:#fff;text-transform:uppercase;margin-bottom:13px}
.col p{font-size:8.5px;line-height:12.3px;color:var(--footer-text)}
.contact-line{display:flex;align-items:center;gap:12px;color:#fff;font-size:8.5px;margin-top:7px}
.tweet{position:relative;padding-left:25px;margin-bottom:14px}
.tweet .bird{position:absolute;left:5px;top:3px;width:9px;height:9px;border-radius:50%;background:var(--teal)}
.tweet .time{color:var(--teal)}
.signup{margin-top:15px;display:flex}
.signup .field{width:97px;height:21px;background:#222;color:#aaa;font-size:8px;line-height:21px;padding-left:9px}
.signup .go{width:27px;height:21px;background:var(--teal);color:#fff;font-size:8px;line-height:21px;text-align:center}
.bottom{left:0;top:1245px;width:989px;height:55px;background:var(--footer-bottom)}
.copy{left:207px;top:21px;font-size:8.5px;color:var(--footer-text)}
.social{position:absolute;top:18px;width:18px;height:18px;border-radius:50%;background:#ddd}
.social.primary{background:#4fb3e0}
</style>
</head>
<body>
<div class="stage">
<div class="page">
  <div class="stripe" style="top:0;height:4px"><span class="s1"></span><span class="s2"></span><span class="s3"></span><span class="s4"></span><span class="s5"></span></div>

  <header>
    <div class="abs brand">
      <div class="brand-dot"></div>
      <div class="brand-text"><div class="l1">VELMAR TILE FLOOR</div><div class="l2">DESIGN COMPETITION</div><div class="l3">2014</div></div>
    </div>
    <nav class="abs nav"><a>Home</a><a>Finalists</a><a>Jury</a><a>Sponsors</a><a>Announcements</a><a>Press</a><a>Blog</a><a>About</a><a>Contact</a></nav>
    <div class="abs account">Sign up<span>|</span>Register</div>
  </header>

  <section class="abs hero" role="img" aria-label="Blurred photo of a warm wooden floor interior">
    <div class="abs badge"><svg width="8" height="8" viewBox="0 0 8 8"><rect x="0.5" y="1.5" width="7" height="6" fill="none" stroke="#fff"/><rect x="0.5" y="1.5" width="7" height="2" fill="#fff"/></svg>NOVEMBER 2013</div>
    <h1 class="abs">1st Annual Velmar Tile Floor Design Competition</h1>
    <p class="abs">In January 2014, Velmar Tile Inc. will launch its 1st Annual Velmar Tile Floor Design Competition. This design competition will be open to Design and Architecture students of the NYC area. Students and student groups can submit cork flooring design concepts...</p>
    <div class="abs btn">READ MORE</div>
  </section>

  <section>
    <div class="abs sec-head" style="left:208px;top:521px">
      <svg width="13" height="13" viewBox="0 0 13 13"><circle cx="6.5" cy="6.5" r="6" fill="var(--teal)"/><path d="M3 4c2 0 2 2 4 2s1 3 0 4M8 2c0 2 2 2 3 2" stroke="#fff" fill="none"/></svg>Announcements
    </div>
    <div class="abs rule" style="left:204px;top:543px;width:381px"></div>
    <div class="abs ann-title">1st Annual Velmar Tile Floor Design Competition</div>
    <div class="abs meta" style="left:204px;top:619px">3 hours ago</div>
    <div class="abs excerpt">Lorem Ipsum is simply dummy text of the printing and typesetting industry... <a>Read more</a></div>
    <div class="abs" role="img" aria-label="Photo of the New York City skyline" style="left:352px;top:556px;width:232px;height:154px;background:linear-gradient(180deg,#8fb6d6 0%,#b8cfe0 35%,#7a756c 60%,#4b4a48 100%)"></div>
  </section>

  <aside class="abs press">
    <div class="abs sec-head" style="left:14px;top:17px">
      <svg width="13" height="13" viewBox="0 0 13 13"><circle cx="2.5" cy="10.5" r="1.6" fill="var(--teal)"/><path d="M1 5a7 7 0 0 1 7 7M1 1a11 11 0 0 1 11 11" stroke="var(--teal)" stroke-width="1.8" fill="none"/></svg>Press Release
    </div>
    <div class="abs rule" style="left:10px;top:39px;width:187px"></div>
    <div class="press-item" style="top:52px"><div class="thumb" role="img" aria-label="City towers photo" style="background:linear-gradient(180deg,#9ec0dd,#8a7f6e)"></div><div class="txt">A New Yorker doesn't necessarily come from...</div><div class="meta">3 minutes ago</div></div>
    <div class="press-item" style="top:107px"><div class="thumb" role="img" aria-label="Portrait photo of an older man" style="background:linear-gradient(180deg,#d9d4cf,#5b5350)"></div><div class="txt">A New Yorker never looks up...</div><div class="meta">7 hours ago</div></div>
    <div class="press-item" style="top:162px"><div class="thumb" role="img" aria-label="Photo of colourful objects on a desk" style="background:linear-gradient(180deg,#c96a5c,#e8ddd3)"></div><div class="txt">A New Yorker doesn't take cabs</div><div class="meta">23 hours ago</div></div>
  </aside>

  <section>
    <div class="abs sec-head" style="left:208px;top:725px">
      <svg width="13" height="13" viewBox="0 0 13 13"><path d="M3 1h7v4a3.5 3.5 0 0 1-7 0zM6.5 8.5v2M4 12h5" stroke="var(--teal)" stroke-width="1.6" fill="var(--teal)"/></svg>Finalists
    </div>
    <div class="abs rule" style="left:204px;top:751px;width:187px"></div>
    <div class="finalist" style="left:205px"><div class="photo" role="img" aria-label="Portrait photo of finalist Aron Kessler" style="background:linear-gradient(180deg,#d8d6d2,#8a7d72 60%,#2b2b30)"></div><div class="name">Aron Kessler, NYC</div></div>
    <div class="finalist" style="left:353px"><div class="photo" role="img" aria-label="Portrait photo of finalist Mira Coleman" style="background:linear-gradient(180deg,#4a4340,#b48f7c 55%,#6b5248)"></div><div class="name">Mira Coleman, NYC</div></div>
    <div class="finalist" style="left:501px"><div class="photo" role="img" aria-label="Portrait photo of finalist Dario Fenn" style="background:linear-gradient(180deg,#e7e5e2,#b69680 55%,#e8e6e3)"></div><div class="name">Dario Fenn, NYC</div></div>
    <div class="finalist" style="left:648px"><div class="photo" role="img" aria-label="Portrait photo of finalist Helen Marsh" style="background:linear-gradient(180deg,#bdbcb8,#8f7465 55%,#3a3a3e)"></div><div class="name">Helen Marsh, NYC</div></div>
  </section>

  <section class="abs band">
    <span class="partner" style="left:197px">Norvik</span>
    <span class="partner" style="left:269px;font-size:12px;top:25px">Brightline Suite</span>
    <span class="partner" style="left:394px">Calvera</span>
    <span class="partner" style="left:492px">Quorant</span>
    <span class="partner" style="left:612px">Tessmark</span>
    <span class="partner" style="left:725px">Lumeo</span>
  </section>

  <div class="stripe" style="top:1027px;height:10px"><span class="s1"></span><span class="s2"></span><span class="s3"></span><span class="s4"></span><span class="s5"></span></div>

  <footer class="abs footer">
    <div class="abs foot-brand"><div class="dot"></div><div class="l1">VELMAR TILE FLOOR</div><div class="l2">DESIGN COMPETITION</div><div class="l3">2014</div></div>
    <div class="abs col" style="left:340px;top:34px;width:135px">
      <h3>Contact</h3>
      <p>There are many variations of passages of Lorem Ipsum availa-ble, but the majority have suf-</p>
      <div class="contact-line" style="margin-top:12px"><svg width="10" height="12" viewBox="0 0 10 12"><path d="M5 12S1 7 1 4.5a4 4 0 0 1 8 0C9 7 5 12 5 12z" fill="var(--teal)"/><circle cx="5" cy="4.5" r="1.5" fill="#111"/></svg>Riverton</div>
      <div class="contact-line"><svg width="11" height="9" viewBox="0 0 11 9"><rect width="11" height="9" fill="var(--teal)"/><path d="M0 0l5.5 5L11 0" stroke="#111" fill="none"/></svg>info@velmartile.com</div>
      <div class="contact-line"><svg width="10" height="10" viewBox="0 0 10 10"><path d="M1 1l2.5-.5 1.2 2.5-1.4 1a6 6 0 0 0 2.7 2.7l1-1.4L9.5 6.5 9 9C4.5 9 1 5.5 1 1z" fill="var(--teal)"/></svg>555-01234-56789</div>
    </div>
    <div class="abs col" style="left:488px;top:34px;width:150px">
      <h3>Latest Tweets</h3>
      <div class="tweet"><span class="bird"></span><p>Lorem Ipsum is simply dummy text of the printing and typeset-ting industry. Lorem Ipsum has<br><span class="time">1 Hour Ago</span></p></div>
      <div class="tweet"><span class="bird"></span><p>Lorem Ipsum is simply dummy text of the printing and typeset-<br><span class="time">1 Hour Ago</span></p></div>
    </div>
    <div class="abs col" style="left:650px;top:34px;width:130px">
      <h3>News Letter</h3>
      <p>Type your email address below and recive our daily news letter for free</p>
      <div class="signup"><div class="field">Email Address</div><div class="go">GO</div></div>
    </div>
  </footer>

  <div class="abs bottom">
    <div class="abs copy">© 2013 All rights reserved.&nbsp; Velmar Tile Floor</div>
    <span class="social primary" style="left:722px"></span>
    <span class="social" style="left:745px"></span>
    <span class="social" style="left:767px"></span>
  </div>
</div>
</div>
</body>
</html>
```